Visit card

Industry/Entity Type

Health Care

Contact Information for Business Card

O VITALIS SYSTEMS
Odile Brevard - chef de Projet

Requirements
Must have
• 318 Gaston Lemaire Street 59710 NORVELLE Tel: 33 (0) 327 481 605 Mobile: 06 42 19 37 64 Web: www.quorvexsystems.example Contact: o.brevard@o-vitalissystems.example
Should not have
• Respect for color

```html
<!DOCTYPE html>
<html lang="fr">
<head>
<meta charset="utf-8">
<title>O Vitalis Systems — Cartes de visite</title>
<link href="https://fonts.googleapis.com/css2?family=Arimo:wght@400;700&display=swap" rel="stylesheet">
<style>
  :root {
    --stage: #1e1e20;
    --card-dark: #4a4a4d;
    --card-dark-ink: #38383a;
    --card-light: #ffffff;
    --band-grey: #4a4a4c;
    --accent-red: #e3232b;
    --ink: #3a3a3c;
    --ink-soft: #2c2c2e;
  }
  * { box-sizing: border-box; margin: 0; padding: 0; }
  html, body { width: 1200px; height: 800px; overflow: hidden; }
  body {
    background: var(--stage);
    font-family: "Arimo", Arial, sans-serif;
    display: flex;
    align-items: center;
    justify-content: center;
    gap: 40px;
  }
  .card {
    position: relative;
    width: 540px;
    height: 310px;
    border-radius: 22px;
    overflow: hidden;
  }

  /* Back side */
  .card--back { background: var(--card-dark); }
  .back-brand {
    position: absolute;
    left: 70px; top: 105px;
    display: flex; align-items: center; gap: 18px;
  }
  .back-brand .brand-dot {
    width: 64px; height: 64px; border-radius: 50%;
    background: var(--card-dark-ink);
  }
  .back-brand .brand-name {
    color: var(--card-dark-ink);
    font-weight: 700;
    font-size: 30px;
    letter-spacing: 1px;
    line-height: 1;
  }
  .back-web {
    position: absolute;
    left: 0; right: 0; top: 218px;
    text-align: center;
    color: var(--card-dark-ink);
    font-size: 14px;
    letter-spacing: 3px;
  }

  /* Front side */
  .card--front { background: var(--card-light); }
  .front-shape { position: absolute; inset: 0; }
  .front-brand {
    position: absolute;
    left: 34px; top: 58px;
    display: flex; align-items: center; gap: 14px;
  }
  .front-brand .brand-dot {
    width: 58px; height: 58px; border-radius: 50%;
    background: var(--accent-red);
  }
  .front-brand .brand-name {
    color: var(--ink);
    font-weight: 700;
    font-size: 26px;
    letter-spacing: 1px;
    line-height: 1;
  }
  .front-details {
    position: absolute;
    left: 40px; top: 134px;
    color: var(--ink-soft);
    font-size: 12.5px;
    line-height: 1.3;
  }
  .person-name { font-weight: 700; font-size: 17px; color: var(--ink-soft); line-height: 1.1; }
  .person-role { color: var(--accent-red); font-size: 14px; margin-bottom: 6px; }
  .address { margin-bottom: 5px; }
  .contact-list { list-style: none; }
  .contact-list li { display: flex; align-items: center; gap: 7px; margin-bottom: 2px; }
  .contact-icon { width: 14px; height: 14px; flex: none; }
</style>
</head>
<body>

  <section class="card card--back" aria-label="Verso de la carte">
    <div class="back-brand">
      <span class="brand-dot"></span>
      <span class="brand-name">O VITALIS SYSTEMS</span>
    </div>
    <p class="back-web">www.quorvexsystems.example</p>
  </section>

  <section class="card card--front" aria-label="Recto de la carte">
    <svg class="front-shape" viewBox="0 0 540 310" width="540" height="310" aria-hidden="true">
      <rect width="540" height="310" fill="var(--band-grey)"/>
      <path d="M230 0 L340 0 C420 25 470 70 500 140 L477 127 Z" fill="var(--accent-red)"/>
      <path d="M0 0 L230 0 C420 30 520 140 540 270 L540 310 L0 310 Z" fill="var(--card-light)"/>
    </svg>

    <div class="front-brand">
      <span class="brand-dot"></span>
      <span class="brand-name">O VITALIS SYSTEMS</span>
    </div>

    <div class="front-details">
      <p class="person-name">ODILE BREVARD</p>
      <p class="person-role">Chef de Projet</p>
      <p class="address">318 Gaston Lemaire Street<br>59710 NORVELLE</p>
      <ul class="contact-list">
        <li>
          <svg class="contact-icon" viewBox="0 0 14 14"><circle cx="7" cy="7" r="6.2" fill="none" stroke="var(--accent-red)" stroke-width="1.2"/><path d="M4.6 3.8 L5.8 3.8 L6.3 5.4 L5.5 6 C5.9 7 6.8 7.9 7.8 8.3 L8.4 7.5 L10 8 L10 9.2 C7 9.6 4.2 6.8 4.6 3.8 Z" fill="var(--accent-red)"/></svg>
          <span>33 (0) 327 481 605</span>
        </li>
        <li>
          <svg class="contact-icon" viewBox="0 0 14 14"><circle cx="7" cy="7" r="6.2" fill="none" stroke="var(--accent-red)" stroke-width="1.2"/><rect x="5" y="3.6" width="4" height="6.8" rx="0.8" fill="none" stroke="var(--accent-red)" stroke-width="1"/></svg>
          <span>06 42 19 37 64</span>
        </li>
        <li>
          <svg class="contact-icon" viewBox="0 0 14 14"><circle cx="7" cy="7" r="7" fill="var(--accent-red)"/><rect x="3.8" y="4.8" width="6.4" height="4.4" fill="#fff"/><path d="M3.8 4.8 L7 7.3 L10.2 4.8" fill="none" stroke="var(--accent-red)" stroke-width="0.8"/></svg>
          <span>o.brevard@o-vitalissystems.example</span>
        </li>
      </ul>
    </div>
  </section>

</body>
</html>
```